Development of the overall look and feel for the website. www.ReelPalsHub.com

This site is geared as a competitor to some of the major Fan websites. Where we want to be different is making a site geared more towards interaction with the Fans in the Social Media platform.
-Live streaming
-Instant Messaging
-Ability to request and purchase custom digital pieces
-Ability for Models/creators to sell blogs, podcasts, clips, screensavers, etc. through a dedicated online digital store.
-We will also have story like features similar to those found on Photoburst to allow interaction.
-Content Creators keep 85% of earnings

This should be sexy, seductive, bold, and geared towards all spectrums. From Swingers, Kink, Fetish, Milf, College, etc.

Overall the feeling should be Fun with a sense of excitement that is taboo and erotic while not scaring people away.

Trying to find the perfect blend between finding harmony/Norma Whitcombe/GBT/SoloPatron/Velvet Soiree and KRV. Monetization will be most similar to SoloPatron.

Target Market(s)

Target market should be 18+ / All Genders/ All sexuality. I want to be sure to target markets that were traditionally left out from some of the bigger platforms with all lifestyle and gender inclusion.

Industry/Entity Type

Adult Modeling, Adult Website, Streaming, Porn/fetish

Colors

Designer to choose colors to be used in the design.

Requirements
Must have
• Sex Appeal, Curiosity, Call to action, Storyboard to tell what we are about
Nice to have
• uploaded some designs that have overall look/feel.
Should not have
• Sexy but no nudity

```html
<!DOCTYPE html>
<html lang="en">
<head>
<meta charset="utf-8">
<title>ReelPalsHub — Live Studio</title>
<link rel="stylesheet" href="https://fonts.googleapis.com/css2?family=Montserrat:wght@500;600;700&family=Open+Sans:wght@400;600&family=Roboto:wght@400&display=swap">
<style>
  :root {
    --plum: #7a2a74;
    --plum-soft: #9b5a96;
    --ink: #111111;
    --muted: #9a9a9a;
    --bubble: #f4f4f6;
    --white: #ffffff;
    --page: #ffffff;
    --video-dark: #1a1416;
    --video-warm: #7a5444;
  }
  * { box-sizing: border-box; margin: 0; padding: 0; }
  html, body { width: 1200px; height: 800px; overflow: hidden; background: var(--page); }
  body { position: relative; font-family: "Montserrat", sans-serif; color: var(--ink); }

  .sidebar { position: absolute; left: 15px; top: 17px; width: 99px; height: 705px; border-radius: 50px; background: var(--plum); }
  .brand { position: absolute; left: 26px; top: 44px; width: 78px; height: 78px; border-radius: 50%; background: var(--white); display: flex; align-items: center; justify-content: center; text-align: center; font-weight: 700; font-size: 12px; line-height: 1.2; color: var(--plum); }
  .nav-pill { position: absolute; z-index: 3; left: 28px; top: 182px; width: 184px; height: 55px; border-radius: 28px; background: var(--white); display: flex; align-items: center; gap: 16px; padding-left: 20px; font-weight: 600; font-size: 15px; white-space: nowrap; box-shadow: 0 4px 14px rgba(0,0,0,.08); }
  .nav-icon { position: absolute; left: 50px; width: 30px; height: 30px; }

  .page-header { position: absolute; left: 153px; top: 26px; display: flex; align-items: center; gap: 28px; }
  .page-title { font-weight: 600; font-size: 24px; letter-spacing: 0; white-space: nowrap; }
  .tier-badge { position: relative; width: 66px; height: 27px; border-radius: 6px; background: var(--plum); color: var(--white); font-weight: 600; font-size: 14px; display: flex; align-items: center; justify-content: center; flex: none; }
  .status-dot { position: absolute; right: -9px; top: -6px; width: 6px; height: 6px; border-radius: 50%; background: #c8c8c8; }

  .account { position: absolute; right: 22px; top: 34px; display: flex; align-items: center; gap: 10px; font-family: "Roboto", sans-serif; font-size: 15px; }
  .lang { display: flex; align-items: center; gap: 4px; margin-right: 18px; }
  .avatar { border-radius: 50%; background: linear-gradient(160deg, #8c7a70, #3d332f); flex: none; }

  .stream { position: absolute; z-index: 1; left: 136px; top: 101px; width: 732px; height: 593px; border-radius: 52px; overflow: hidden; background: radial-gradient(ellipse at 60% 35%, var(--video-warm) 0%, #3a2a26 45%, var(--video-dark) 80%); }
  .live-tag { position: absolute; z-index: 2; left: 759px; top: 132px; width: 80px; }
  .live-tag span { display: block; color: var(--white); font-size: 10px; font-weight: 600; padding: 2px 8px; }
  .live-tag .live { background: var(--plum); width: 48px; margin-left: 10px; }
  .live-tag .streaming { background: #2b2b2b; }

  .controls { position: absolute; z-index: 2; left: 259px; top: 680px; width: 502px; height: 70px; border-radius: 18px; background: var(--white); box-shadow: 0 6px 22px rgba(0,0,0,.1); }
  .ctrl { position: absolute; top: 11px; width: 49px; height: 51px; border-radius: 8px; background: var(--white); box-shadow: 0 2px 8px rgba(0,0,0,.08); display: flex; align-items: center; justify-content: center; }
  .end-stream { position: absolute; left: 186px; top: 11px; width: 134px; height: 51px; border-radius: 6px; background: var(--plum); color: var(--white); font-weight: 600; font-size: 14px; display: flex; align-items: center; justify-content: center; }

  .chat { position: absolute; left: 889px; top: 105px; width: 305px; height: 675px; border-radius: 30px; background: var(--white); box-shadow: 0 4px 26px rgba(0,0,0,.05); }
  .chat-title { position: absolute; left: 28px; top: 18px; font-weight: 600; font-size: 19px; }
  .stats { position: absolute; left: 7px; top: 60px; width: 292px; height: 214px; border-radius: 30px; background: var(--plum); color: var(--white); padding: 20px 27px; }
  .stats h2 { font-weight: 500; font-size: 17px; line-height: 1.35; }
  .metric { margin-top: 24px; }
  .metric + .metric { margin-top: 30px; }
  .metric-row { display: flex; justify-content: space-between; font-weight: 600; font-size: 11px; }
  .track { margin-top: 12px; height: 5px; border-radius: 3px; background: var(--plum-soft); }
  .fill { height: 100%; border-radius: 3px; background: var(--white); }

  .message { position: absolute; left: 29px; width: 265px; height: 71px; }
  .message .avatar { position: absolute; left: 0; top: 18px; width: 48px; height: 48px; }
  .message .bubble { position: absolute; left: 50px; top: 0; width: 195px; height: 71px; border-radius: 6px; background: var(--bubble); padding: 10px 18px; }
  .bubble h3 { font-weight: 600; font-size: 13.5px; }
  .bubble p { font-family: "Open Sans", sans-serif; font-size: 10px; color: var(--muted); line-height: 1.5; margin-top: 5px; }
  .tone-b { background: linear-gradient(160deg, #c98d68, #6b3a2a); }
</style>
</head>
<body>

<nav class="sidebar" aria-label="Main navigation"></nav>
<div class="brand">ReelPals<br>Hub</div>

<div class="nav-pill">
  <svg width="30" height="30" viewBox="0 0 30 30" fill="none" stroke="#7a2a74" stroke-width="1.5"><rect x="9" y="3" width="13" height="12" rx="1"/><path d="M12 7h7M12 10h7"/><circle cx="8" cy="22" r="4"/><path d="M12 22h10M22 22v-7"/></svg>
  <span>SELL BLOGS</span>
</div>

<svg class="nav-icon" style="top:277px" viewBox="0 0 30 30" fill="none" stroke="#fff" stroke-width="1.5"><rect x="5" y="8" width="8" height="13" rx="4"/><path d="M3 16a6 6 0 0 0 12 0M9 22v4M6 27h6"/><rect x="16" y="3" width="12" height="8" rx="2"/><path d="M19 6h6M19 8h4"/></svg>
<svg class="nav-icon" style="top:344px" viewBox="0 0 30 30" fill="none" stroke="#fff" stroke-width="1.6"><path d="M20 8l-9 9a3 3 0 0 0 4 4l10-10a5 5 0 0 0-7-7L7 15a7 7 0 0 0 10 10l8-8"/></svg>
<svg class="nav-icon" style="top:409px" viewBox="0 0 30 30" fill="none" stroke="#fff" stroke-width="1.4"><rect x="5" y="5" width="20" height="20"/><path d="M13 17l-5 5M8 18v4h4M17 13l5-5M18 8h4v4"/></svg>
<svg class="nav-icon" style="top:480px" viewBox="0 0 30 30" fill="#fff"><circle cx="7" cy="15" r="2.5"/><circle cx="15" cy="15" r="2.5"/><circle cx="23" cy="15" r="2.5"/></svg>
<svg class="nav-icon" style="top:592px" viewBox="0 0 30 30" fill="#fff"><path d="M16 8h8a2 2 0 0 1 2 2v10a2 2 0 0 1-2 2h-8v-2h8V10h-8z"/><path d="M4 15l7-6v4h8v4h-8v4z"/></svg>

<header class="page-header">
  <h1 class="page-title">Lorem ipsum dolor sit amet</h1>
  <div class="tier-badge">PRO<span class="status-dot"></span></div>
</header>

<div class="account">
  <svg width="18" height="18" viewBox="0 0 18 18" fill="none" stroke="#111" stroke-width="1.3"><path d="M4 13V8a5 5 0 0 1 10 0v5l1 1H3zM7.5 16h3"/></svg>
  <div class="lang">EN <svg width="12" height="10" viewBox="0 0 12 10"><path d="M0 0h12L6 10z" fill="#111"/></svg></div>
  <div class="avatar" style="width:40px;height:40px" role="img" aria-label="Profile photo of the streamer"></div>
  <span>Mirela Voss</span>
</div>

<div class="stream" role="img" aria-label="Live stream video: close-up of a model in black lace stockings holding a red rope on dark satin"></div>
<div class="live-tag"><span class="live">LIVE ▸</span><span class="streaming">STREAMING</span></div>

<div class="controls">
  <div class="ctrl" style="left:58px"><svg width="22" height="16" viewBox="0 0 22 16" fill="#b2245a"><rect x="0" y="2" width="14" height="12" rx="2"/><path d="M15 6l7-4v12l-7-4z"/></svg></div>
  <div class="ctrl" style="left:122px"><svg width="14" height="20" viewBox="0 0 14 20" fill="none" stroke="#b2245a" stroke-width="1.8"><rect x="4" y="1" width="6" height="11" rx="3" fill="#b2245a"/><path d="M1 9a6 6 0 0 0 12 0M7 15v4"/></svg></div>
  <div class="end-stream">End Streaming</div>
  <div class="ctrl" style="left:337px"><svg width="20" height="20" viewBox="0 0 20 20" fill="#b2245a"><rect x="7" y="1" width="12" height="12" rx="2"/><rect x="1" y="7" width="12" height="12" rx="2" stroke="#fff" stroke-width="1.5"/></svg></div>
  <div class="ctrl" style="left:400px"><svg width="20" height="18" viewBox="0 0 20 18" fill="none" stroke="#b2245a" stroke-width="1.8"><rect x="1" y="1" width="18" height="16" rx="2"/><path d="M1 6h18M1 11h18M6 1v16"/></svg></div>
</div>

<aside class="chat">
  <h2 class="chat-title">Chat</h2>
  <section class="stats">
    <h2>Fans on the Social Media platform</h2>
    <div class="metric">
      <div class="metric-row"><span>Fans</span><span>50%</span></div>
      <div class="track"><div class="fill" style="width:53%"></div></div>
    </div>
    <div class="metric">
      <div class="metric-row"><span>Liks</span><span>60%</span></div>
      <div class="track"><div class="fill" style="width:60%"></div></div>
    </div>
  </section>

  <div class="message" style="top:300px">
    <div class="avatar" role="img" aria-label="Fan profile photo"></div>
    <div class="bubble"><h3>Callum Reyes</h3><p>Lorem ipsum dolor sit amet, con-<br>sectetur adipiscing</p></div>
  </div>
  <div class="message" style="top:392px">
    <div class="avatar tone-b" role="img" aria-label="Fan profile photo"></div>
    <div class="bubble"><h3>Sabine Orlo</h3><p>Lorem ipsum dolor sit amet, con-<br>sectetur adipiscing</p></div>
  </div>
  <div class="message" style="top:484px">
    <div class="avatar" role="img" aria-label="Fan profile photo"></div>
    <div class="bubble"><h3>Callum Reyes</h3><p>Lorem ipsum dolor sit amet, con-<br>sectetur adipiscing</p></div>
  </div>
  <div class="message" style="top:577px">
    <div class="avatar tone-b" role="img" aria-label="Fan profile photo"></div>
    <div class="bubble"><h3>Sabine Orlo</h3><p>Lorem ipsum dolor sit amet, con-<br>sectetur adipiscing</p></div>
  </div>
</aside>

</body>
</html>
```